Food broker, trader, wholesaler, liquidator looking for a 5 pages website

Looking for a 5 pages website design. We are food brokers, traders, wholesaler and closeout buyer working with manufacturers, distributors, importers sell to retailers, food service operators and industrial (ingredients). We help market their products. We are a resource for those who need a solution in the distribution/selling/placement of food on the shelves, kitchens and pantries. Whether we open new accounts with new products or sell short dated inventory, we know where to go and get results.

Target Market(s)

Food manufacturers, food distributors, food brokers

Coding

Coded - Design and coding required

Number of Pages Required

4 page

Font styles to use
Serif

Requirements
Must have
• Food-food production-warehouse-Food packaging-people meeting-trucks-supermarket shelves-

```html
<!DOCTYPE html>
<html lang="en">
<head>
<meta charset="utf-8">
<title>Harvest Lane Trading</title>
<link rel="stylesheet" href="https://fonts.googleapis.com/css2?family=Noto+Serif:wght@400;700&family=Merriweather:wght@400;700&family=Raleway:wght@400;500&display=swap">
<style>
:root{
  --navy:#0d1565;
  --navy-soft:#1c2577;
  --ink:#333;
  --muted:#6a6a6a;
  --line:#dcdcdc;
  --footer:#2b2b2b;
  --white:#fff;
}
*{box-sizing:border-box;margin:0;padding:0}
html,body{width:1200px;height:3617px;overflow:hidden;background:var(--white)}
body{position:relative;font-family:"Merriweather",serif;color:var(--ink)}
.abs{position:absolute}
.brand-name{font-family:"Noto Serif",serif;font-weight:700;color:var(--navy);font-size:19px;letter-spacing:.3px}
.site-header{position:absolute;left:0;top:0;width:1200px;height:115px;background:var(--white)}
.brand{position:absolute;left:112px;top:38px;display:flex;align-items:center;gap:10px}
.brand-dot{width:26px;height:26px;border-radius:50%;background:var(--navy)}
.main-nav a{position:absolute;top:48px;font-family:"Noto Serif",serif;font-size:14px;color:#333;text-decoration:none}
.main-nav a.active{color:var(--navy)}
.hero{position:absolute;left:0;top:115px;width:1200px;height:685px;background:linear-gradient(100deg,#8d9a6e 0%,#c7b59b 30%,#6f7f9c 55%,#b9a88c 80%,#d7c19a 100%)}
.hero-box{position:absolute;left:629px;top:404px;width:500px;height:273px;background:rgba(60,60,70,.55);text-align:center;color:var(--white);padding-top:22px}
.hero-box h1{font-family:"Noto Serif",serif;font-weight:400;font-size:45px;line-height:1.2}
.hero-box p{font-size:16px;line-height:37px;margin-top:6px;padding:0 30px}
.btn{display:inline-block;background:var(--navy);color:var(--white);font-family:"Noto Serif",serif;font-size:15px;text-decoration:none}
.hero-box .btn{margin-top:14px;padding:14px 25px}
.dots{position:absolute;left:586px;top:776px;display:flex;gap:8px}
.dots span{width:9px;height:9px;border-radius:50%;background:#555}
.dots span.on{background:var(--navy);width:16px;border-radius:5px}
.sec-title{position:absolute;left:0;width:1200px;text-align:center;font-family:"Noto Serif",serif;font-weight:400;font-size:39px;color:var(--navy)}
.sec-sub{position:absolute;left:0;width:1200px;text-align:center;font-size:15px;color:#555}
.step-label{position:absolute;font-family:"Noto Serif",serif;font-size:19px;line-height:33px;color:#333}
.about{position:absolute;left:0;top:1663px;width:1200px;height:484px}
.about-panel{position:absolute;left:0;top:0;width:682px;height:484px;background:var(--navy);color:var(--white)}
.about-panel h2{position:absolute;left:139px;top:68px;font-family:"Noto Serif",serif;font-weight:400;font-size:46px}
.about-rule{position:absolute;left:139px;top:139px;width:60px;height:3px;background:var(--white)}
.about-panel p{position:absolute;left:139px;top:170px;width:468px;font-size:12.4px;line-height:30px;text-align:justify}
.btn-outline{position:absolute;left:139px;top:376px;width:131px;height:49px;border:1px solid var(--white);border-radius:3px;color:var(--white);font-family:"Noto Serif",serif;font-size:14px;display:flex;align-items:center;justify-content:center}
.about-photo{position:absolute;left:682px;top:0;width:518px;height:484px;background:linear-gradient(160deg,#c9ccd3,#8a93a6 50%,#5a6278)}
.service-card{position:absolute;top:2310px;width:309px;height:392px;border:1px solid #e6e6e6;background:var(--white);text-align:center;box-shadow:0 0 6px rgba(0,0,0,.04)}
.service-img{position:absolute;left:10px;top:10px;width:289px;height:215px}
.service-card h3{position:absolute;left:0;top:252px;width:100%;font-family:"Noto Serif",serif;font-weight:400;font-size:19px;color:#333}
.service-card .rule{position:absolute;left:133px;top:290px;width:42px;height:2px;background:var(--navy)}
.service-card p{position:absolute;left:20px;top:308px;width:269px;font-family:"Raleway",sans-serif;font-size:13px;line-height:25px;color:var(--muted)}
.contact{position:absolute;left:0;top:2762px;width:1200px;height:480px;background:linear-gradient(180deg,#f1efec,#e9e5df)}
.field{position:absolute;background:var(--white);border:1px solid #d6d6d6;font-size:12px;color:#555;padding:15px 16px}
.site-footer{position:absolute;left:0;top:3242px;width:1200px;height:375px;background:var(--footer);color:var(--white)}
.footer-brand{position:absolute;left:0;top:148px;width:500px;text-align:center;display:flex;justify-content:center;align-items:center;gap:10px}
.footer-brand .brand-name{color:var(--white);font-size:20px}
.footer-brand .brand-dot{background:var(--white)}
.footer-col h4{position:absolute;top:48px;font-family:"Noto Serif",serif;font-weight:400;font-size:23px}
.footer-list{position:absolute;top:98px;list-style:none;font-family:"Raleway",sans-serif;font-size:14px}
.footer-list li{height:35px;padding-left:27px;position:relative}
.footer-list li::before{content:"»";position:absolute;left:0;top:-2px}
.newsletter p{position:absolute;left:836px;top:98px;width:260px;font-family:"Raleway",sans-serif;font-size:14px;line-height:25px}
.news-field{position:absolute;left:836px;top:171px;width:250px;height:42px;background:var(--white);color:#555;font-family:"Raleway",sans-serif;font-size:13px;padding:12px 14px}
.news-btn{position:absolute;left:836px;top:223px;width:96px;height:32px;background:var(--navy);font-family:"Raleway",sans-serif;font-size:14px;display:flex;align-items:center;justify-content:center}
.footer-rule{position:absolute;left:112px;top:298px;width:976px;height:1px;background:#444}
.copyright{position:absolute;left:0;top:326px;width:1200px;text-align:center;font-family:"Raleway",sans-serif;font-size:13px}
</style>
</head>
<body>

<header class="site-header">
  <div class="brand"><span class="brand-dot"></span><span class="brand-name">HARVEST LANE TRADING</span></div>
  <nav class="main-nav">
    <a class="active" style="left:583px">Home</a>
    <a style="left:671px">About Us</a>
    <a style="left:779px">What we do</a>
    <a style="left:907px">Contact</a>
    <a style="left:1006px">Giving Back</a>
  </nav>
</header>

<section class="hero" role="img" aria-label="Family shopping with a trolley in a supermarket aisle">
  <div class="hero-box">
    <h1>Harvest Lane</h1>
    <p>Sed ut perspiciatis unde omnis iste natus error sit voluptatem accusantium doloremque laudantium, totam rem aperiam</p>
    <a class="btn">Read More</a>
  </div>
  <div class="dots"><span></span><span class="on"></span><span></span></div>
</section>

<h2 class="sec-title" style="top:843px">Our Process</h2>
<p class="sec-sub" style="top:915px">Sed ut perspiciatis unde omnis iste natus error sit voluptatem accusantium doloremque</p>

<svg class="abs" style="left:0;top:960px" width="1200" height="680" viewBox="0 960 1200 680" fill="none" stroke="#0d1565" stroke-width="3">
  <defs>
    <marker id="arrowhead" markerWidth="12" markerHeight="12" refX="9" refY="6" orient="auto">
      <path d="M1 1 L10 6 L1 11" stroke="#0d1565" stroke-width="1.6" fill="none"/>
    </marker>
  </defs>
  <g marker-end="url(#arrowhead)">
    <path d="M622 1044 Q685 1050 722 1074"/>
    <path d="M822 1158 Q845 1200 860 1252"/>
    <path d="M860 1380 Q848 1428 812 1480"/>
    <path d="M708 1560 Q652 1585 566 1582"/>
    <path d="M446 1536 Q404 1505 380 1466"/>
    <path d="M332 1350 Q326 1293 338 1236"/>
    <path d="M406 1124 Q446 1085 498 1064"/>
  </g>
  <g stroke-width="2">
    <circle cx="557" cy="1050" r="54"/>
    <circle cx="770" cy="1114" r="54"/>
    <circle cx="858" cy="1325" r="54"/>
    <circle cx="762" cy="1523" r="54"/>
    <circle cx="505" cy="1565" r="54"/>
    <circle cx="344" cy="1416" r="54"/>
    <circle cx="363" cy="1176" r="54"/>
  </g>
  <g stroke-width="2.2">
    <rect x="536" y="1030" width="40" height="32" rx="3"/><circle cx="556" cy="1046" r="8"/><path d="M550 1062 v12 M562 1062 v12"/>
    <path d="M748 1110 L770 1094 L792 1110 V1138 H748 Z M758 1138 V1120 H782 V1138"/>
    <rect x="838" y="1308" width="40" height="36" rx="4"/><path d="M838 1318 H878 M846 1330 q12 -8 24 0 q-12 8 -24 0"/>
    <circle cx="762" cy="1506" r="8"/><circle cx="746" cy="1512" r="6"/><circle cx="778" cy="1512" r="6"/><path d="M740 1544 v-18 q22 -12 44 0 v18"/>
    <rect x="478" y="1548" width="32" height="26"/><path d="M510 1556 h14 l8 10 v8 h-22"/><circle cx="488" cy="1578" r="5"/><circle cx="522" cy="1578" r="5"/>
    <path d="M322 1400 H366 V1436 H322 Z M322 1412 H366 M322 1424 H366"/>
    <path d="M338 1182 H388 Q386 1200 363 1200 Q340 1200 338 1182 Z M348 1178 q15 -22 30 0 M355 1176 q8 -12 16 0"/>
  </g>
  <circle cx="587" cy="1284" r="40" fill="#0d1565" stroke="none"/>
</svg>
<span class="step-label" style="left:394px;top:979px">Food<br>Production</span>
<span class="step-label" style="left:842px;top:1094px">Warehouse</span>
<span class="step-label" style="left:927px;top:1286px">Food<br>Packaging</span>
<span class="step-label" style="left:834px;top:1497px">People<br>Meeting</span>
<span class="step-label" style="left:378px;top:1563px">Trucks</span>
<span class="step-label" style="left:153px;top:1393px">Supermarket<br>Shelves</span>
<span class="step-label" style="left:245px;top:1155px">Food</span>

<section class="about">
  <div class="about-panel">
    <h2>About Us</h2>
    <div class="about-rule"></div>
    <p>Harvest Lane Trading works with food manufacturers, brand owners, distributors and wholesalers market their products. Retail, Food Service and Industrial ingredients.Founded in 2008, Harvest Lane Trading started with the distribution of gluten free products understanding the need to provide access to unique flavors and products forthe celiac consumers. From this, we expanded into deli, dairy, groceries, frozen and beverages.</p>
    <div class="btn-outline">READ MORE</div>
  </div>
  <div class="about-photo" role="img" aria-label="Smiling warehouse manager holding a clipboard between tall shelving racks"></div>
</section>

<h2 class="sec-title" style="top:2190px">What We Do</h2>
<p class="sec-sub" style="top:2253px">Sed ut perspiciatis unde omnis iste natus error sit voluptatem accusantium doloremque</p>

<article class="service-card" style="left:112px">
  <div class="service-img" role="img" aria-label="Sales team meeting in an office with market charts" style="background:linear-gradient(135deg,#3d4a5e,#8a96a8 60%,#d6dbe2)"></div>
  <h3>Sales &amp; Marketing</h3><div class="rule"></div>
  <p>we connect food buyers and sellers through a dedicated approach.</p>
</article>
<article class="service-card" style="left:445px">
  <div class="service-img" role="img" aria-label="Hands typing on a laptop beside trading screens" style="background:linear-gradient(135deg,#2c3a52,#5e6f86 50%,#b79a6e)"></div>
  <h3>Trading</h3><div class="rule"></div>
  <p>we purchase goods anywhere and ship them Nationwide and Export.</p>
</article>
<article class="service-card" style="left:779px">
  <div class="service-img" role="img" aria-label="Warehouse aisle with pallets of boxes and a forklift" style="background:linear-gradient(135deg,#c48a4e,#a9b4c4 50%,#d9a86a)"></div>
  <h3>Closeout/Excess Inventory</h3><div class="rule"></div>
  <p>we buy closeouts and excess inventory for prisons, outlet stores and discounters.</p>
</article>

<section class="contact" role="img" aria-label="Faded warehouse background">
  <h2 class="sec-title" style="top:50px">Contact Us</h2>
  <p class="sec-sub" style="top:112px">Sed ut perspiciatis unde omnis iste natus error sit voluptatem accusantium</p>
  <div class="field" style="left:281px;top:161px;width:313px;height:44px">First Name :</div>
  <div class="field" style="left:606px;top:161px;width:313px;height:44px">Last Name :</div>
  <div class="field" style="left:281px;top:218px;width:313px;height:44px">Email :</div>
  <div class="field" style="left:606px;top:218px;width:313px;height:44px">Phone :</div>
  <div class="field" style="left:281px;top:273px;width:638px;height:85px;padding-top:12px">Message :</div>
  <div class="btn abs" style="left:526px;top:381px;width:148px;height:48px;display:flex;align-items:center;justify-content:center;font-size:14px">SUBMIT</div>
</section>

<footer class="site-footer">
  <div class="footer-brand"><span class="brand-dot"></span><span class="brand-name">HARVEST LANE TRADING</span></div>
  <div class="footer-col"><h4 style="left:396px">Quick Links</h4>
    <ul class="footer-list" style="left:396px"><li>Home</li><li>About Us</li><li>What we do</li><li>Contact</li><li>Giving Back</li></ul></div>
  <div class="footer-col"><h4 style="left:612px">Services</h4>
    <ul class="footer-list" style="left:612px"><li>Sed ut perspiciatis</li><li>unde omnis iste</li><li>natus error sit</li><li>voluptatem</li><li>accusantium</li></ul></div>
  <div class="footer-col newsletter"><h4 style="left:836px">Newsletter</h4>
    <p>Sed ut perspiciatis unde omnis iste natus error sit voluptatem</p>
    <div class="news-field">Email :</div>
    <div class="news-btn">SUBMIT</div></div>
  <div class="footer-rule"></div>
  <p class="copyright">© Copyright 2020 Harvest Lane Trading.All Rights Reserved</p>
</footer>

</body>
</html>
```